The quiet harbor with an elephant incorporated in the background

Target Market(s)

Real estate

Industry/Entity Type

Real Estate

Contact Information for Business Card

On back on want my name & number
In front I want the business name, "the quiet harbor", below to say staging & design

Logo Text

The quiet harbor

Font styles to use
Serif

Colors
000000

Requirements
Must have
• I want an elephant behind the writing in gold transperant

```html
<!DOCTYPE html>
<html lang="en">
<head>
<meta charset="UTF-8">
<title>The Quiet Harbor – Business Card</title>
<link rel="stylesheet" href="https://fonts.googleapis.com/css2?family=Cormorant+Garamond:wght@500;600;700&display=swap">
<style>
  :root {
    --backdrop: #1a1a1a;
    --card: #1f1f1f;
    --gold: #c9a24a;
    --gold-light: #e6c776;
    --gold-deep: #8e6b22;
    --white: #ffffff;
  }
  * { margin: 0; padding: 0; box-sizing: border-box; }
  html, body {
    width: 1200px;
    height: 1000px;
    overflow: hidden;
    background: var(--backdrop);
    font-family: "Cormorant Garamond", serif;
  }
  .canvas {
    position: relative;
    width: 1200px;
    height: 1000px;
  }
  .card {
    position: absolute;
    left: 215px;
    width: 770px;
    height: 440px;
    background: var(--card);
    overflow: hidden;
  }
  .card--front { top: 40px; }
  .card--back { top: 520px; }

  /* Front */
  .elephant-head {
    position: absolute;
    left: 175px;
    top: 10px;
    width: 420px;
    height: 430px;
    background: radial-gradient(closest-side at 50% 45%, rgba(230,199,118,0.85) 0%, rgba(201,162,74,0.7) 45%, rgba(142,107,34,0.35) 75%, rgba(31,31,31,0) 100%);
  }
  .brand-frame {
    position: absolute;
    left: 170px;
    top: 140px;
    width: 430px;
    height: 74px;
    border: 2px solid var(--white);
    display: flex;
    align-items: center;
    justify-content: center;
    background: rgba(31,31,31,0.15);
  }
  .brand-name {
    color: var(--white);
    font-weight: 600;
    font-size: 22px;
    letter-spacing: 0.38em;
    text-transform: uppercase;
    padding-left: 0.38em;
    white-space: nowrap;
  }
  .brand-tagline {
    position: absolute;
    left: 0;
    top: 232px;
    width: 100%;
    text-align: center;
    color: var(--white);
    font-weight: 500;
    font-size: 16px;
    letter-spacing: 0.32em;
    padding-left: 0.32em;
    text-transform: uppercase;
  }

  /* Back */
  .elephant-figure {
    position: absolute;
    left: 330px;
    top: 95px;
    width: 170px;
    height: 70px;
    border-radius: 40px 40px 6px 6px;
    background: linear-gradient(180deg, var(--gold-light) 0%, var(--gold) 60%, var(--gold-deep) 100%);
  }
  .name-frame {
    position: absolute;
    left: 205px;
    top: 165px;
    width: 360px;
    height: 100px;
    border: 2px solid var(--gold);
    display: flex;
    align-items: center;
    justify-content: center;
  }
  .person-name {
    color: var(--gold);
    font-weight: 700;
    font-size: 38px;
    letter-spacing: 0.06em;
    text-transform: uppercase;
    white-space: nowrap;
  }
  .contact {
    position: absolute;
    left: 0;
    top: 292px;
    width: 100%;
    text-align: center;
  }
  .contact-icon {
    display: block;
    margin: 0 auto 6px;
  }
  .contact-phone {
    color: var(--white);
    font-weight: 500;
    font-size: 22px;
    letter-spacing: 0.03em;
  }
</style>
</head>
<body>
<main class="canvas">
  <section class="card card--front">
    <div class="elephant-head" role="img" aria-label="Translucent gold foil elephant head illustration behind the business name"></div>
    <div class="brand-frame">
      <span class="brand-name">The quiet harbor</span>
    </div>
    <p class="brand-tagline">Staging &amp; Design</p>
  </section>

  <section class="card card--back">
    <div class="elephant-figure" role="img" aria-label="Small gold elephant figure with raised trunk standing on the frame"></div>
    <div class="name-frame">
      <span class="person-name">Daniel Reyes</span>
    </div>
    <div class="contact">
      <svg class="contact-icon" width="14" height="14" viewBox="0 0 24 24" aria-hidden="true">
        <path fill="#c9a24a" d="M6.6 10.8a15.1 15.1 0 0 0 6.6 6.6l2.2-2.2a1 1 0 0 1 1-.25 11.4 11.4 0 0 0 3.6.57 1 1 0 0 1 1 1V20a1 1 0 0 1-1 1A17 17 0 0 1 3 4a1 1 0 0 1 1-1h3.5a1 1 0 0 1 1 1c0 1.25.2 2.450.57 3.6a1 1 0 0 1-.25 1z"/>
      </svg>
      <span class="contact-phone">+000 987 654 321</span>
    </div>
  </section>
</main>
</body>
</html>
```